Birchline Septic Solutions

Would like to see some single sided ones but would also like to see some double sided with one sided only being the logo. Owners name is Colin Vandro. Phone number is 555-214-0387
Services are pumping, inspections, installs, and repairs

Contact Information for Business Card

555-241-0387 Colin Vandro Maple Hollow, OH

```html
<!DOCTYPE html>
<html lang="en">
<head>
<meta charset="utf-8">
<title>Birchline Septic Solutions — Business Cards</title>
<link href="https://fonts.googleapis.com/css2?family=Arimo:wght@400;700&display=swap" rel="stylesheet">
<style>
  :root {
    --ink: #2a2a2a;
    --teal: #2bb5aa;
    --grey: #8c8c8c;
    --paper: #ffffff;
    --table: #e9e9e9;
  }
  * { margin: 0; padding: 0; box-sizing: border-box; }
  html, body { width: 1200px; height: 802px; overflow: hidden; }
  body {
    background: var(--table);
    font-family: "Arimo", Arial, sans-serif;
    display: flex;
    align-items: center;
    justify-content: center;
    gap: 40px;
  }
  .card {
    position: relative;
    width: 540px;
    height: 309px;
    background: var(--paper);
    border-bottom: 4px solid var(--teal);
    box-shadow: 0 6px 18px rgba(0,0,0,0.12);
    overflow: hidden;
  }

  /* Front card */
  .corner-tab {
    position: absolute;
    top: 0; right: 0;
    width: 18px; height: 26px;
    background: var(--teal);
  }
  .owner {
    position: absolute;
    top: 26px; right: 34px;
    text-align: right;
  }
  .owner-name {
    color: var(--teal);
    font-weight: 700;
    font-size: 19px;
    letter-spacing: 0.5px;
  }
  .owner-role {
    color: var(--grey);
    font-size: 13px;
    margin-top: 2px;
  }
  .front-brand {
    position: absolute;
    left: 34px; top: 108px;
  }
  .brand-lockup {
    display: flex;
    align-items: center;
    gap: 10px;
  }
  .brand-mark {
    flex: none;
    width: 14px; height: 14px;
    background: var(--teal);
  }
  .brand-name {
    color: var(--ink);
    font-weight: 700;
    font-size: 17px;
    letter-spacing: 2px;
    text-transform: uppercase;
    line-height: 1.25;
  }
  .contact {
    position: absolute;
    left: 48px; bottom: 38px;
    font-size: 14px;
  }
  .contact-city { color: var(--grey); margin-bottom: 6px; }
  .contact-phone {
    color: var(--ink);
    font-weight: 700;
    display: flex;
    align-items: center;
    gap: 6px;
  }
  .contact-phone svg { width: 13px; height: 13px; }
  .front-scene {
    position: absolute;
    right: 0; bottom: 0;
    width: 260px; height: 220px;
    background: linear-gradient(200deg, rgba(42,42,42,0.15) 0%, rgba(42,42,42,0.85) 70%);
  }

  /* Back card */
  .back-logo {
    position: absolute;
    left: 50%; top: 50%;
    transform: translate(-50%, -50%);
    display: flex;
    flex-direction: column;
    align-items: center;
    gap: 14px;
  }
  .back-scene {
    width: 230px; height: 70px;
    background: linear-gradient(180deg, rgba(42,42,42,0.25) 0%, rgba(42,42,42,0.8) 100%);
  }
  .back-logo .brand-name { font-size: 22px; text-align: center; }
</style>
</head>
<body>

  <section class="card card-front">
    <div class="corner-tab"></div>
    <div class="owner">
      <div class="owner-name">COLIN VANDRO</div>
      <div class="owner-role">Owners</div>
    </div>
    <div class="front-brand brand-lockup">
      <span class="brand-mark"></span>
      <span class="brand-name">Birchline<br>Septic Solutions</span>
    </div>
    <div class="contact">
      <div class="contact-city">Maple Hollow, OH</div>
      <div class="contact-phone">
        <svg viewBox="0 0 16 16" aria-hidden="true"><circle cx="8" cy="8" r="7.5" fill="var(--teal)"/><path d="M5.2 4.2l1.3-.3.8 1.9-.9.7c.5 1 1.2 1.7 2.2 2.2l.7-.9 1.9.8-.3 1.3c-3.2.2-6-2.6-5.7-5.7z" fill="#fff"/></svg>
        555-214-0387
      </div>
    </div>
    <div class="front-scene" role="img" aria-label="Illustration of rocky mountain peaks with a line of pine trees"></div>
  </section>

  <section class="card card-back">
    <div class="back-logo">
      <div class="back-scene" role="img" aria-label="Illustration of a mountain ridge with pine trees"></div>
      <div class="brand-lockup">
        <span class="brand-mark"></span>
        <span class="brand-name">Birchline<br>Septic Solutions</span>
      </div>
    </div>
  </section>

</body>
</html>
```